Torvane Halbridge

Looking for modern business cards.
Clean contemporary design.
Similar to this.
https://www.plumvexa-search.example/imgres?imgurl=https%3A%2F%2Fimg.quorlint-cdn.example%2Fsleek_dark_metal_card_design_540.jpg&imgrefurl=https%3A%2F%2Fwww.quorlint-prints.example%2Fsleek_dark_metal_card_design-918273645501928374&q=modern%20business%20cards

But I'd like the blue to look metallic.

Business

```html
<!DOCTYPE html>
<html lang="en">
<head>
<meta charset="utf-8">
<title>Torvane Halbridge – Business Cards</title>
<link rel="stylesheet" href="https://fonts.googleapis.com/css2?family=Arimo:wght@400;700&display=swap">
<style>
  :root {
    --stage: #272727;
    --card-white: #ffffff;
    --navy: #1d4e6b;
    --steel: #245a78;
    --cyan: #1a9fc6;
    --ink: #1e1e1e;
    --metal-deep: #1e5d7c;
    --metal-mid: #1a93b6;
    --metal-hi: #27a9cb;
    --alert: #e8321e;
  }
  * { margin: 0; padding: 0; box-sizing: border-box; }
  html, body {
    width: 1200px; height: 900px; overflow: hidden;
    background: var(--stage);
    font-family: "Arimo", Arial, sans-serif;
  }
  .stage { position: relative; width: 1200px; height: 900px; }

  .card {
    position: absolute; top: 306px;
    width: 440px; height: 271px;
    overflow: hidden;
    box-shadow: 2px 3px 6px rgba(0,0,0,0.55);
  }
  .card-front { left: 149px; background: var(--card-white); }
  .card-back {
    left: 608px;
    background:
      linear-gradient(120deg, rgba(255,255,255,0) 35%, rgba(255,255,255,0.08) 48%, rgba(255,255,255,0) 60%),
      radial-gradient(ellipse 75% 90% at 50% 40%, var(--metal-hi) 0%, var(--metal-mid) 45%, var(--metal-deep) 100%);
  }

  .name-marker { position: absolute; left: 0; top: 26px; width: 30px; height: 37px; }
  .holder-name {
    position: absolute; left: 37px; top: 28px;
    font-size: 16px; font-weight: 700; letter-spacing: 0.2px;
    color: var(--navy);
  }
  .holder-name .surname { color: var(--cyan); }
  .holder-title {
    position: absolute; left: 37px; top: 46px;
    font-size: 13px; color: var(--ink);
  }

  .brand { position: absolute; white-space: nowrap; }
  .brand-name { font-size: 27px; font-weight: 400; letter-spacing: -0.5px; display: flex; align-items: center; gap: 8px; }
  .brand-dot { width: 10px; height: 10px; border-radius: 50%; display: inline-block; }
  .brand-tagline { font-size: 6px; margin-top: 1px; padding-left: 1px; }

  .card-front .brand { right: 24px; top: 118px; }
  .card-front .brand-name { color: var(--navy); }
  .card-front .brand-dot { background: var(--alert); }
  .card-front .brand-tagline { color: var(--cyan); }

  .card-back .brand { left: 88px; top: 136px; }
  .card-back .brand-name { color: #ffffff; }
  .card-back .brand-dot { background: #ffffff; }
  .card-back .brand-tagline { color: #ffffff; }

  .contact-list {
    position: absolute; left: 24px; top: 195px;
    list-style: none; font-size: 13px; color: var(--ink);
  }
  .contact-list li { display: flex; align-items: center; gap: 5px; height: 16.5px; }
  .contact-list svg { width: 10px; height: 10px; fill: var(--steel); }

  .address {
    position: absolute; right: 23px; top: 213px;
    font-size: 13px; line-height: 16px; text-align: right; color: var(--ink);
    font-style: normal;
  }

  .footer-bands { position: absolute; left: 0; bottom: 0; width: 440px; height: 20px; }
</style>
</head>
<body>
<main class="stage">

  <section class="card card-front" aria-label="Card front">
    <svg class="name-marker" viewBox="0 0 30 37">
      <polygon points="0,0 10,0 16,37 0,37" fill="var(--cyan)"/>
      <polygon points="12,0 28,0 28,37 18,37" fill="var(--steel)"/>
    </svg>
    <h1 class="holder-name">ELRIC <span class="surname">DAWSONE</span></h1>
    <p class="holder-title">Managing Director</p>

    <div class="brand">
      <div class="brand-name">Torvane Halbridge <span class="brand-dot"></span></div>
      <div class="brand-tagline">Steady Guidance for Every Growing Company</div>
    </div>

    <ul class="contact-list">
      <li><svg viewBox="0 0 10 10"><path d="M1 3c0-1 1-2 4-2s4 1 4 2v1H7V3H3v1H1zM2 5h6l1 4H1z"/></svg>444 555 6688</li>
      <li><svg viewBox="0 0 10 10"><path d="M0 2h10v6H0zM1 3l4 3 4-3" stroke="#fff" stroke-width="0.8"/></svg>info@halbridge.example</li>
      <li><svg viewBox="0 0 10 10"><circle cx="5" cy="5" r="4.6"/></svg>www.halbridge.example</li>
    </ul>

    <address class="address">421, Address line here<br>Country Name,45452</address>

    <svg class="footer-bands" viewBox="0 0 440 20">
      <polygon points="0,7 196,7 186,20 0,20" fill="var(--cyan)"/>
      <polygon points="212,1 440,1 440,20 198,20" fill="var(--steel)"/>
    </svg>
  </section>

  <section class="card card-back" aria-label="Card back">
    <div class="brand">
      <div class="brand-name">Torvane Halbridge <span class="brand-dot"></span></div>
      <div class="brand-tagline">Steady Guidance for Every Growing Company</div>
    </div>
  </section>

</main>
</body>
</html>
```